I need a flyer made , the flyer can be one page or two pages or three pages . I will be posting this on Instagram and social media platforms. I am a luxury home builder , I am looking to hire a construction project manager . Below are some examples and ideas what can be on the flyer

We’re looking for a construction project manager who’s passionate about building luxury homes at the highest standards
We’re hiring construction project manager
* Experience 5+ years in residential project management with a strong portfolio of completed homes.
* location : Bergen County NJ
* excellent leadership skills, leads teams with confidence and clarity
* communicates seamlessly with architects , engineers, designers and clients
*knows how to manage budgets and timelines without compromising quality
*solves problems with a positive solution first mindset
* pays attention to every detail because in luxury the small things are the big things

Apply now , link in bio or DM to connect.

My logo is attached, my web site www.velstridebuilders.com
My style is modern but still warm and inviting. I like a clean classy look .

Please don’t add any images of chairs or people to the flyer , I do not want people on my flyer. Do not add standard images of offices and houses , we are luxury builders , we build homes over 2 million dollars. Keep a classy , simple modern look . High end .

You can add a white hard hat with my logo on it for a image , this is a suggestion does not have to be on my flyer ,

```html
<!DOCTYPE html>
<html lang="en">
<head>
<meta charset="utf-8">
<title>We're Hiring – Construction Project Manager</title>
<link href="https://fonts.googleapis.com/css2?family=Allura&family=League+Spartan:wght@300;700;800;900&family=Poppins:wght@300;400;600;700;800&display=swap" rel="stylesheet">
<style>
  :root{
    --backdrop:#5f5f5f;
    --paper:#f4f4f4;
    --paper-shade:#e2e2e2;
    --ink:#0b0b0b;
    --ink-soft:#333333;
    --panel-left:#050505;
    --panel-right:#2a2a2a;
    --tag-dark:#0d0d0d;
    --tag-grey:#474747;
    --pin-red:#e01d1d;
    --pin-deep:#b30f12;
    --white:#ffffff;
    --tick:#cfcfcf;
  }
  *{margin:0;padding:0;box-sizing:border-box}
  html,body{width:1200px;height:956px;overflow:hidden;background:var(--backdrop)}
  .flyer{
    position:absolute;left:88px;top:137px;width:1024px;height:683px;overflow:hidden;
    background:radial-gradient(ellipse at 70% 20%,#ffffff 0%,var(--paper) 45%,var(--paper-shade) 100%);
    font-family:"Poppins",sans-serif;color:var(--ink);
  }
  .sketch-area{
    position:absolute;left:0;top:40px;width:390px;height:620px;
    background:linear-gradient(100deg,rgba(200,200,200,.45) 0%,rgba(225,225,225,.35) 60%,rgba(240,240,240,0) 100%);
  }
  .pin{position:absolute;left:335px;top:84px;width:138px;height:210px}
  .pin-label{
    position:absolute;left:380px;top:132px;width:72px;text-align:center;
    font:700 13px/15px "Poppins",sans-serif;color:var(--ink);
  }
  .headline{position:absolute;left:478px;top:30px;width:420px;height:200px}
  .script{font-family:"Allura",cursive;fill:var(--ink-soft)}
  .hiring{font-family:"League Spartan",sans-serif;font-weight:900;fill:var(--ink)}
  .role{position:absolute;left:482px;top:232px;width:262px;height:70px}
  .role text{font-family:"League Spartan",sans-serif;font-size:36px}
  .role .construction{font-weight:800;fill:var(--ink-soft)}
  .role .manager{font-weight:300;fill:var(--ink)}
  .role .manager tspan{font-weight:800}
  .tag{
    position:absolute;left:755px;width:141px;height:27px;border-radius:3px 14px 14px 3px;
    color:var(--white);font:300 13px/27px "Poppins",sans-serif;padding-left:10px;
  }
  .tag b{font-weight:700}
  .tag.luxury{top:239px;background:var(--tag-dark)}
  .tag.excellence{top:270px;height:28px;line-height:28px;background:var(--tag-grey)}
  .requirements{
    position:absolute;left:330px;top:329px;width:639px;height:176px;border-radius:24px;overflow:hidden;
    display:flex;color:var(--white);
  }
  .req-col{list-style:none;padding:24px 20px 0 26px}
  .req-col.left{width:319px;background:var(--panel-left)}
  .req-col.right{flex:1;background:var(--panel-right);padding-left:14px;padding-right:40px}
  .req-col li{position:relative;padding-left:15px;font-size:12.6px;line-height:14.7px;font-weight:400;margin-bottom:9.5px}
  .req-col li b{font-weight:700}
  .req-col li::before{
    content:"";position:absolute;left:0;top:3px;width:9px;height:9px;border-radius:50%;background:var(--tick);
  }
  .req-col li::after{
    content:"";position:absolute;left:2.5px;top:5px;width:3px;height:2px;
    border-left:1.5px solid var(--panel-left);border-bottom:1.5px solid var(--panel-left);transform:rotate(-45deg);
  }
  .cta{position:absolute;top:527px;height:40px;border-radius:20px;font-weight:700;text-align:center}
  .cta.apply{left:405px;width:166px;top:528px;height:38px;background:var(--ink);color:var(--white);font-size:20px;line-height:34px;z-index:1}
  .cta.connect{left:566px;width:329px;border:1px solid #9a9a9a;background:rgba(255,255,255,.6);color:var(--ink);font-size:19.5px;line-height:40px}
  .contact-heading{position:absolute;top:589px;font:700 20px/1 "Poppins",sans-serif;color:var(--ink)}
  .contact-line{position:absolute;top:614px;font:400 18px/24px "Poppins",sans-serif;color:var(--ink);display:flex;align-items:center;white-space:nowrap}
  .dot{display:inline-block;width:14px;height:14px;border-radius:50%;background:var(--ink-soft);margin-right:6px}
  .divider{position:absolute;left:689px;top:594px;width:1px;height:43px;background:#8a8a8a}
</style>
</head>
<body>
<main class="flyer">
  <div class="sketch-area" role="img" aria-label="Light line drawing of a modern luxury house facade"></div>

  <svg class="pin" viewBox="0 0 138 210" aria-hidden="true">
    <defs>
      <radialGradient id="pinFill" cx="35%" cy="25%" r="80%">
        <stop offset="0" stop-color="#ff5a52"/><stop offset=".55" stop-color="#e01d1d"/><stop offset="1" stop-color="#b30f12"/>
      </radialGradient>
    </defs>
    <ellipse cx="66" cy="205" rx="30" ry="4" fill="rgba(0,0,0,.25)"/>
    <path d="M69 2C32 2 3 31 3 68c0 45 50 98 62 136 12-38 70-91 70-136C135 31 106 2 69 2z" fill="url(#pinFill)"/>
    <circle cx="81" cy="70" r="37" fill="#c41317"/>
    <circle cx="81" cy="70" r="35" fill="#ffffff"/>
  </svg>
  <p class="pin-label">Bergen County, NJ</p>

  <svg class="headline" viewBox="0 0 420 200" aria-label="We're Hiring">
    <text class="script" x="4" y="92" font-size="104" textLength="188" lengthAdjust="spacingAndGlyphs">We're</text>
    <text class="hiring" x="2" y="184" font-size="124" textLength="412" lengthAdjust="spacingAndGlyphs">HIRING</text>
  </svg>

  <svg class="role" viewBox="0 0 262 70" role="heading" aria-level="1" aria-label="Construction Project Manager">
    <text class="construction" x="1" y="30" textLength="258" lengthAdjust="spacingAndGlyphs">CONSTRUCTION</text>
    <text class="manager" x="1" y="66" textLength="259" lengthAdjust="spacingAndGlyphs">PROJECT <tspan>MANAGER</tspan></text>
  </svg>
  <div class="tag luxury">BUILD <b>LUXURY</b></div>
  <div class="tag excellence">LEAD <b>EXCELLENCE</b></div>

  <section class="requirements">
    <ul class="req-col left">
      <li>Experience <b>5+ years</b> in residential project management with a strong portfolio of completed homes.</li>
      <li>Excellent <b>leadership skills</b>, leads teams with confidence and clarity</li>
      <li><b>Communicates seamlessly</b> with architects , engineers, designers and clients</li>
    </ul>
    <ul class="req-col right">
      <li>Knows how to <b>manage budgets and timelines</b> without compromising quality</li>
      <li><b>Solves problems</b> with a positive solution first mindset</li>
      <li><b>Pays attention to every detail</b> because in luxury the small things are the big things</li>
    </ul>
  </section>

  <div class="cta apply">Apply now</div>
  <div class="cta connect">Link in bio or DM to connect</div>

  <h2 class="contact-heading" style="left:333px">Follow us</h2>
  <p class="contact-line" style="left:332px"><span class="dot"></span>velstridebuilders</p>
  <p class="contact-line" style="left:539px"><span class="dot"></span>VelstrideHQ</p>
  <div class="divider"></div>
  <h2 class="contact-heading" style="left:716px">Visit us</h2>
  <p class="contact-line" style="left:716px">www.velstridebuilders.com</p>
</main>
</body>
</html>
```